Business card design needed

I would like a one sided black business card with the information provided above. Refer to my website www.brightvolleyracquets.com.au for an example of colors I have used for my site, would like to keep this consistent for my business cards also, I will upload my logo below.

I am a new small business that provides tennis customers with racquet re stringing, tennis strings and accessories.

Industry/Entity Type

Small Business

Contact Information for Business Card

Bright Volley Tennis

Owen Whitby
Managing Director

brightvolleyracquets@mailbox.example
www.brightvolleyracquets.com.au
0491 726 305

Racquet Restringing/Tennis Strings/Accessories

Requirements
Must have
• Must have my logo and card must be black

```html
<!DOCTYPE html>
<html lang="en">
<head>
<meta charset="utf-8">
<title>Bright Volley Tennis – Business Card</title>
<link rel="stylesheet" href="https://fonts.googleapis.com/css2?family=Open+Sans:ital,wght@0,400;0,700;1,700&display=swap">
<style>
  :root {
    --backdrop: #5b3b24;
    --card-black: #050505;
    --lime: #b6d433;
    --white: #ffffff;
    --divider: #4a4a4a;
  }
  * { margin: 0; padding: 0; box-sizing: border-box; }
  html, body {
    width: 1200px;
    height: 750px;
    overflow: hidden;
    background: var(--backdrop);
    font-family: "Open Sans", Arial, sans-serif;
  }
  .business-card {
    position: absolute;
    left: 75px;
    top: 75px;
    width: 1050px;
    height: 597px;
    border-radius: 34px;
    background: var(--card-black);
    overflow: hidden;
  }
  .swoosh-bands {
    position: absolute;
    inset: 0;
    width: 1050px;
    height: 597px;
  }
  .swoosh-bands .lime { fill: var(--lime); }

  .brand-mark {
    position: absolute;
    left: 52px;
    top: 158px;
    display: flex;
    align-items: center;
    gap: 18px;
  }
  .brand-mark .brand-dot {
    width: 44px;
    height: 44px;
    border-radius: 50%;
    background: var(--lime);
  }
  .brand-mark .brand-name {
    font-size: 48px;
    font-weight: 700;
    color: var(--lime);
    letter-spacing: 0.5px;
    line-height: 1;
  }

  .contact-block {
    position: absolute;
    left: 52px;
    top: 402px;
    color: var(--white);
  }
  .contact-name {
    color: var(--lime);
    font-size: 27px;
    font-weight: 700;
    line-height: 36px;
    margin-bottom: 8px;
  }
  .contact-name .role {
    font-size: 22px;
    font-weight: 400;
  }
  .contact-line {
    font-size: 22px;
    line-height: 44px;
  }
  .contact-line .label {
    font-weight: 700;
    font-style: italic;
  }

  .service-divider {
    position: absolute;
    left: 524px;
    top: 475px;
    width: 1px;
    height: 86px;
    background: var(--divider);
  }
  .service-list {
    position: absolute;
    left: 560px;
    top: 464px;
    list-style: none;
    color: var(--white);
    font-size: 24px;
    line-height: 36px;
  }
  .service-list li {
    display: flex;
    align-items: center;
  }
  .service-list li::before {
    content: "";
    width: 8px;
    height: 8px;
    background: var(--white);
    margin-right: 10px;
  }
</style>
</head>
<body>
  <div class="business-card">
    <svg class="swoosh-bands" viewBox="0 0 1050 597" aria-hidden="true">
      <path class="lime" d="M725,0 L790,0 C890,70 985,260 940,520 C975,300 880,90 725,0 Z"/>
      <path class="lime" d="M860,0 C975,80 1025,320 880,597 L1050,597 L1050,0 Z"/>
    </svg>

    <div class="brand-mark">
      <span class="brand-dot"></span>
      <span class="brand-name">Bright Volley Tennis</span>
    </div>

    <div class="contact-block">
      <p class="contact-name">Owen Whitby, <span class="role">Managing Director</span></p>
      <p class="contact-line"><span class="label">phone</span> 0491 726 305</p>
      <p class="contact-line"><span class="label">email</span> brightvolleyracquets@mailbox.example</p>
      <p class="contact-line"><span class="label">web</span> www.brightvolleyracquets.com.au</p>
    </div>

    <div class="service-divider"></div>
    <ul class="service-list">
      <li>Racquet Restringing</li>
      <li>Tennis Strings</li>
      <li>Accessories</li>
    </ul>
  </div>
</body>
</html>
```